New Dental Office Needs an Attractive and user friendly Website Designed

I need a website for a new dental office. The Name is Harrowfield Dentistry. I would like a Modern design with a user friendly interface and usability.
I would like a landing page, a page that lists the services we offer: Cosmetic Dentistry, Implants, Dental Hygiene, Emergency Services, Restorations, Dentures
Target Market(s)
Mid to upper class
Industry/Entity Type
Dentistry
Coding
Number of Pages Required
1 page
Requirements
Must have
- Landing page that has a scheduling option, Procedures, operating hours, and contact us info
Nice to have
- Appealing design, Soft comforting colors. Easy to navigate page, Modern and professional.

```html
<!DOCTYPE html>
<html lang="en">
<head>
<meta charset="utf-8">
<title>Harrowfield Dentistry</title>
<link href="https://fonts.googleapis.com/css2?family=Poppins:wght@400;500;600&display=swap" rel="stylesheet">
<style>
:root{
  --gold:#9c8259;
  --teal:#3f7479;
  --teal-soft:#9ab9bb;
  --cream:#f4f2ee;
  --ink:#222222;
  --muted:#555555;
  --faint:#9a9a9a;
  --line:#d9d6cf;
  --footer:#343434;
}
*{box-sizing:border-box;margin:0;padding:0}
html,body{width:1200px;height:3840px;overflow:hidden}
body{font-family:'Poppins',sans-serif;color:var(--ink);background:#fff;position:relative}
.abs{position:absolute}
section{position:absolute;left:0;width:1200px}
.btn{position:absolute;display:flex;align-items:center;justify-content:center;border-radius:6px;color:#fff;font-size:13px;font-weight:500;background:var(--gold)}
.btn.teal{background:var(--teal)}
.eyebrow{color:var(--teal);font-size:13px}
.center{text-align:center;left:0;width:1200px}
.h2{font-size:33px;font-weight:600}
.lead{font-size:14px;color:var(--muted);line-height:20px}
.ph{position:absolute}

/* header */
.logo{font-size:22px;font-weight:500;color:var(--ink);display:flex;align-items:center;gap:8px}
.logo i{width:10px;height:10px;background:var(--gold);display:block}
.nav a{position:absolute;top:32px;font-size:14px;color:var(--ink);text-decoration:none}
.nav a.active{color:var(--teal)}

/* hero */
.hero{top:0;height:648px;background:var(--cream)}
.hero h1{position:absolute;left:161px;top:218px;font-size:50px;font-weight:600;line-height:60px}
.hero h1 span{color:var(--gold)}
.hero p{position:absolute;left:161px;top:350px;width:450px;font-size:15px;line-height:18px;color:#333}
.info-card{position:absolute;display:flex;align-items:center;gap:16px;padding:0 22px;border-radius:10px}
.info-card b{display:block;font-size:14px;font-weight:600}
.info-card small{font-size:12px}

/* about */
.about{top:648px;height:608px;background:#fff}
.about p{position:absolute;left:662px;width:370px;font-size:14px;line-height:20px;color:#333}

/* services */
.services{top:1256px;height:626px;background:var(--cream)}
.svc{position:absolute;top:227px;width:213px;height:259px;background:#fff;border-radius:8px;box-shadow:0 2px 10px rgba(0,0,0,.05);text-align:center}
.svc.dim{opacity:.55}
.svc .ico{position:absolute;left:73px;top:29px;width:67px;height:75px;border-radius:6px;background:#ede6da}
.svc h3{position:absolute;top:121px;width:100%;font-size:15px;font-weight:500}
.svc p{position:absolute;top:146px;left:14px;right:14px;font-size:11px;line-height:13px;color:var(--faint)}
.svc .btn{left:41px;top:198px;width:130px;height:34px;font-size:11px}
.arrow{position:absolute;top:1592px;width:40px;height:40px;border-radius:50%;background:var(--gold);display:flex;align-items:center;justify-content:center}

/* testimonials */
.testi{top:1882px;height:723px;background:#fff}
.quote{position:absolute;width:210px;text-align:center}
.quote b{display:block;font-size:15px;font-weight:500;margin-bottom:10px}
.quote p{font-size:12px;line-height:15px;color:#333}
.quote em{display:block;font-style:normal;color:var(--teal);font-size:34px;font-weight:600;line-height:30px;margin-top:8px}

/* team */
.team{top:2605px;height:573px;background:var(--cream)}
.member{position:absolute;top:193px;width:200px;height:245px;border-radius:4px}
.member .tag{position:absolute;left:15px;right:15px;top:164px;height:67px;background:#fff;border-radius:4px;text-align:center;padding-top:12px}
.member .tag b{display:block;font-size:14px;font-weight:500}
.member .tag small{font-size:11px;color:var(--faint)}

/* contact */
.contact{top:3178px;height:350px;background:#fff}
.field{position:absolute;width:176px;font-size:12px;color:#333;border-bottom:1px solid var(--line);padding-bottom:14px}

/* footer */
.footer{top:3528px;height:312px;background:var(--footer);color:#fff}
.footer .links a{position:absolute;top:116px;font-size:12px;color:#fff;text-decoration:none}
.contact-item{position:absolute;top:155px;display:flex;align-items:center;gap:14px;font-size:12px}
.contact-item i{width:26px;height:26px;border-radius:50%;background:var(--gold);display:flex;align-items:center;justify-content:center}
.social{position:absolute;top:211px;width:14px;height:14px;border-radius:50%;border:1.6px solid #fff}
</style>
</head>
<body>

<section class="hero">
  <div class="abs logo" style="left:161px;top:26px">Harrowfield Dentistry<i></i></div>
  <nav class="nav">
    <a class="active" style="left:435px">Home</a>
    <a style="left:511px">About Us</a>
    <a style="left:607px">Services</a>
    <a style="left:696px">Dentists</a>
    <a style="left:778px">Contact Us</a>
  </nav>
  <div class="btn teal" style="left:877px;top:22px;width:162px;height:42px;font-size:14px">Book Appointment</div>

  <h1>High Quality and<br><span>Painless Dentistry</span></h1>
  <p>If you are in need of high-quality, professional and friendly dental care, look no further than our clinic.</p>
  <div class="btn" style="left:161px;top:408px;width:161px;height:40px">Learn More</div>

  <div class="ph" role="img" aria-label="Smiling dentist in white coat with arms crossed, teal leaves and tooth model" style="left:745px;top:104px;width:440px;height:611px;border-radius:220px 220px 30px 30px;background:linear-gradient(180deg,#9ab9bb 0%,#cfdcdc 55%,#e9e9e9 100%)"></div>

  <div class="info-card" style="left:669px;top:390px;width:247px;height:87px;background:var(--gold);color:#fff">
    <svg width="40" height="40" viewBox="0 0 40 40"><circle cx="20" cy="20" r="17" fill="none" stroke="#fff" stroke-width="2.5"/><path d="M20 10v10l6 4" fill="none" stroke="#fff" stroke-width="2.5" stroke-linecap="round"/></svg>
    <div><b>Opening Hours</b><small>Mon to Sat 08:00 - 20:00</small></div>
  </div>
  <div class="info-card" style="left:626px;top:502px;width:247px;height:87px;background:#fff;box-shadow:0 6px 20px rgba(0,0,0,.08)">
    <svg width="38" height="38" viewBox="0 0 24 24"><path d="M6.6 10.8a15.1 15.1 0 0 0 6.6 6.6l2.2-2.2a1 1 0 0 1 1-.25 11.4 11.4 0 0 0 3.6.57 1 1 0 0 1 1 1V20a1 1 0 0 1-1 1A17 17 0 0 1 3 4a1 1 0 0 1 1-1h3.5a1 1 0 0 1 1 1c0 1.25.2 2.45.57 3.57a1 1 0 0 1-.25 1z" fill="var(--teal)"/></svg>
    <div><b>Need Dental Services?</b><small style="color:var(--muted)">Call: +1 555 010 2234</small></div>
  </div>
</section>

<section class="about">
  <div class="ph" role="img" aria-label="Two smiling dental professionals in blue scrubs" style="left:182px;top:60px;width:395px;height:548px;border-radius:198px 198px 0 0;background:linear-gradient(180deg,#dfe3e6 0%,#6f9cc8 60%,#1f4f8a 100%)"></div>
  <div class="ph" role="img" aria-label="Decorative teal leaves" style="left:432px;top:60px;width:180px;height:150px;border-radius:60% 40% 60% 40%;background:#3f7479;opacity:.85"></div>
  <div class="abs eyebrow" style="left:662px;top:156px">About Us</div>
  <div class="abs" style="left:660px;top:183px;font-size:33px;font-weight:500;line-height:38px;width:400px">Professionals and Personalized Dental Excellence</div>
  <p style="top:306px">Welcome to our Harrowfield Chapters dedicated to empowering pet owners with valuable knowledge and resources.</p>
  <p style="top:378px">Welcome to our Harrowfield Chapters dedicated to empowering pet owners with valuable knowledge and resources.</p>
  <div class="btn" style="left:662px;top:460px;width:161px;height:40px">Learn More</div>
</section>

<section class="services">
  <div class="abs eyebrow center" style="top:75px">Our Services</div>
  <div class="abs h2 center" style="top:98px">Complete Care for Every Smile</div>
  <div class="abs lead center" style="top:148px">Welcome to our Harrowfield Chapters dedicated to empowering pet owners with<br>valuable knowledge and resources.</div>

  <div class="svc dim" style="left:21px"><div class="ico" role="img" aria-label="Dentures icon"></div><h3>Emergency Services</h3><p>It is a long established fact that a will be distracted.</p><div class="btn teal">View Details</div></div>
  <div class="svc" style="left:257px"><div class="ico" role="img" aria-label="Implant icon"></div><h3>Implants</h3><p>It is a long established fact that a will be distracted.</p><div class="btn teal">View Details</div></div>
  <div class="svc" style="left:492px"><div class="ico" role="img" aria-label="Sparkling tooth icon"></div><h3>Cosmetic Dentistry</h3><p>It is a long established fact that a will be distracted.</p><div class="btn teal">View Details</div></div>
  <div class="svc" style="left:727px"><div class="ico" role="img" aria-label="Toothbrush and tooth icon"></div><h3>Dental Hygiene</h3><p>It is a long established fact that a will be distracted.</p><div class="btn teal">View Details</div></div>
  <div class="svc dim" style="left:963px"><div class="ico" role="img" aria-label="Dental drill icon"></div><h3>Restorations</h3><p>It is a long established fact that a will be distracted.</p><div class="btn teal">View Details</div></div>

  <div class="btn" style="left:520px;top:534px;width:160px;height:40px">View All Services</div>
</section>
<div class="arrow" style="left:238px"><svg width="12" height="12" viewBox="0 0 12 12"><path d="M8 1 3 6l5 5" fill="none" stroke="#fff" stroke-width="1.8"/></svg></div>
<div class="arrow" style="left:919px"><svg width="12" height="12" viewBox="0 0 12 12"><path d="M4 1l5 5-5 5" fill="none" stroke="#fff" stroke-width="1.8"/></svg></div>

<section class="testi">
  <div class="abs eyebrow center" style="top:64px">Our Testimonial</div>
  <div class="abs h2 center" style="top:100px">Pleasing Patients Is Our Greatest Achievement</div>
  <div class="abs lead center" style="top:140px">Welcome to our Harrowfield Chapters dedicated to empowering pet owners with<br>valuable knowledge and resources.</div>
  <svg class="abs" style="left:225px;top:200px" width="750" height="390" viewBox="0 0 750 390"><path d="M30 380 A345 345 0 0 1 720 380" fill="none" stroke="#f1efea" stroke-width="34" stroke-linecap="round"/></svg>
  <div class="ph" role="img" aria-label="Smiling dentist with stethoscope among gold leaves and tooth model" style="left:388px;top:197px;width:387px;height:477px;border-radius:190px 190px 20px 20px;background:linear-gradient(180deg,#efece6 0%,#c9b48f 55%,#e5e5e5 100%)"></div>

  <div class="quote" style="left:281px;top:226px"><b>Nora K.</b><p>It is a long established fact that a reader will be distracted by the of using Lorem Ipsum.</p><em>&ldquo;</em></div>
  <div class="quote" style="left:706px;top:226px"><b>Nora K.</b><p>It is a long established fact that a reader will be distracted by the of using Lorem Ipsum.</p><em>&ldquo;</em></div>
  <div class="quote" style="left:162px;top:390px"><b>Nora K.</b><p>It is a long established fact that a reader will be distracted by the of using Lorem Ipsum.</p><em>&ldquo;</em></div>
  <div class="quote" style="left:828px;top:390px"><b>Nora K.</b><p>It is a long established fact that a reader will be distracted by the of using Lorem Ipsum.</p><em>&ldquo;</em></div>
</section>

<section class="team">
  <div class="abs eyebrow center" style="top:44px">Meet Our Dental Team</div>
  <div class="abs h2 center" style="top:80px">Committed to Your Smile</div>
  <div class="abs lead center" style="top:118px">Welcome to our Harrowfield Chapters dedicated to empowering pet owners with<br>valuable knowledge and resources.</div>

  <div class="member" role="img" aria-label="Portrait of a dentist in blue scrubs" style="left:161px;background:linear-gradient(180deg,#cfe0ef,#3e7fc8)"><div class="tag"><b>Dr. Clara Whitmore</b><small>Lead Dentist</small></div></div>
  <div class="member" role="img" aria-label="Portrait of a dentist in white coat" style="left:386px;background:linear-gradient(180deg,#c7ccd2,#e6e8ea)"><div class="tag"><b>Dr. Clara Whitmore</b><small>Lead Dentist</small></div></div>
  <div class="member" role="img" aria-label="Portrait of a dentist with dental tools" style="left:611px;background:linear-gradient(180deg,#6fd6ec,#1aa9c9)"><div class="tag"><b>Dr. Clara Whitmore</b><small>Lead Dentist</small></div></div>
  <div class="member" role="img" aria-label="Portrait of a dentist in a clinic" style="left:836px;background:linear-gradient(180deg,#e7ecf1,#bcd0e2)"><div class="tag"><b>Dr. Clara Whitmore</b><small>Lead Dentist</small></div></div>

  <div class="btn" style="left:520px;top:476px;width:160px;height:40px">View All Team</div>
</section>

<section class="contact">
  <div class="abs eyebrow" style="left:161px;top:84px">Contact</div>
  <div class="abs" style="left:161px;top:108px;font-size:40px;font-weight:600">Get In Touch</div>
  <div class="field" style="left:161px;top:184px">First Name*</div>
  <div class="field" style="left:377px;top:184px">Last Name*</div>
  <div class="field" style="left:589px;top:184px;height:123px">Message*</div>
  <div class="field" style="left:161px;top:245px">Phone Number*</div>
  <div class="field" style="left:377px;top:245px">Email Address*</div>
  <div class="ph" role="img" aria-label="Tooth model with dental mirror over pale teal leaves" style="left:767px;top:40px;width:298px;height:254px;border-radius:50% 50% 40% 40%;background:radial-gradient(circle at 50% 50%,#eef0f0 0%,#d6e2e3 70%,#fff 100%)"></div>
  <div class="btn" style="left:805px;top:236px;width:232px;height:34px">Send Message</div>
</section>

<section class="footer">
  <div class="abs logo" style="left:0;width:1200px;justify-content:center;top:44px;color:#fff">Harrowfield Dentistry<i></i></div>
  <div class="links">
    <a style="left:381px">Home</a><a style="left:466px">About Us</a><a style="left:568px">Services</a><a style="left:666px">Team</a><a style="left:752px">Contact Us</a>
  </div>
  <div class="contact-item" style="left:279px"><i><svg width="12" height="12" viewBox="0 0 24 24"><path d="M6.6 10.8a15.1 15.1 0 0 0 6.6 6.6l2.2-2.2a1 1 0 0 1 1-.25 11.4 11.4 0 0 0 3.6.57 1 1 0 0 1 1 1V20a1 1 0 0 1-1 1A17 17 0 0 1 3 4a1 1 0 0 1 1-1h3.5a1 1 0 0 1 1 1c0 1.25.2 2.45.57 3.57a1 1 0 0 1-.25 1z" fill="#fff"/></svg></i>+1 555 014 8888</div>
  <div class="contact-item" style="left:486px"><i><svg width="12" height="12" viewBox="0 0 24 24"><rect x="3" y="5" width="18" height="14" rx="2" fill="none" stroke="#fff" stroke-width="2"/><path d="M3 7l9 6 9-6" fill="none" stroke="#fff" stroke-width="2"/></svg></i>harrowfield.care@mailbox.com</div>
  <div class="contact-item" style="left:747px;top:151px"><i><svg width="12" height="12" viewBox="0 0 24 24"><path d="M12 2a7 7 0 0 0-7 7c0 5 7 13 7 13s7-8 7-13a7 7 0 0 0-7-7z" fill="#fff"/><circle cx="12" cy="9" r="2.5" fill="var(--gold)"/></svg></i>122, Lorem ipsum dolrd</div>
  <div class="social" style="left:549px"></div>
  <div class="social" style="left:593px"></div>
  <div class="social" style="left:635px"></div>
  <div class="abs" style="left:161px;top:257px;width:878px;height:1px;background:#555"></div>
  <div class="abs center" style="top:276px;font-size:11px">Copyright &copy; 2025 harrowfield. All rights reserved.</div>
</section>

</body>
</html>
```